New Business Card Design for Manufacturing

We are an engineering/manufacturing company that offers Advanced machining/assembly/engineering services, as well as innovative products for the heavy duty engine cooling markets.

We are looking to get a new business card designed that is clean and modern looking, but still fits the wide range of technical/skilled work we do.

- We hope to use this design as the base for other design work in new Presentations, web, and print work.

Industry/Entity Type

Engineering

Contact Information for Business Card

Our preferred color of blue is (RGB) 22/71/159 but can vary slightly from that color. Our content will be our Logo and full company name (Vantrell Forge Works, Inc.), company address, name, job title, phone number with extension, cell number, fax number, website, and email address on the cards.
We'd like the full company name next to the logo, but we are open to other interpretations of that layout.
Preferably, we would like the back side to be clean with just our logo, and the front to contain all of the contact information.

Colors
2f74b4
0355a3
85abd2

Requirements
Must have
• - Logo, company name, needed content - We are open to interpretation beyond that.
• - Standard size business card.
• - Horizontal orientation.
• - Enough space for lengthy names / job titles (for example, a job title could read "Directory of Human Resources" or "V.P. of Governmental Affairs"). We need this to look clean, whether the title be short (CEO) or long (as described above).

```html
<!DOCTYPE html>
<html lang="en">
<head>
<meta charset="utf-8">
<title>Vantrell Forge Works – Business Card</title>
<link rel="stylesheet" href="https://fonts.googleapis.com/css2?family=Amaranth:wght@400;700&family=Open+Sans:wght@400;600&display=swap">
<style>
  :root {
    --brand-blue: #0355a3;
    --brand-blue-deep: #024d94;
    --brand-blue-mid: #2f74b4;
    --brand-blue-light: #85abd2;
    --card-white: #f7f7f7;
    --ink: #3a3a3a;
    --backdrop: #e4e4e4;
    --white: #ffffff;
  }
  * { margin: 0; padding: 0; box-sizing: border-box; }
  html, body { width: 1200px; height: 576px; overflow: hidden; }
  body { background: var(--backdrop); position: relative; font-family: "Open Sans", sans-serif; }

  .card {
    position: absolute;
    top: 138px;
    width: 484px;
    height: 294px;
    border-radius: 13px;
  }

  /* Back side */
  .card-back {
    left: 82px;
    background: linear-gradient(180deg, var(--brand-blue) 0%, var(--brand-blue-deep) 100%);
  }
  .card-back .wordmark {
    position: absolute;
    left: 0; right: 0;
    top: 108px;
    text-align: center;
    font-family: "Amaranth", sans-serif;
    font-weight: 700;
    font-size: 40px;
    color: var(--white);
    letter-spacing: 0.5px;
  }
  .card-back .web-line {
    position: absolute;
    left: 0; right: 0;
    top: 265px;
    display: flex;
    align-items: center;
    justify-content: center;
    gap: 10px;
    color: var(--white);
    font-size: 12.5px;
  }
  .card-back .rule {
    width: 52px;
    height: 2px;
    background: var(--white);
    border-radius: 1px;
  }

  /* Front side */
  .card-front {
    left: 602px;
    background: var(--card-white);
  }
  .holder-name {
    position: absolute;
    left: 22px; top: 38px;
    font-family: "Amaranth", sans-serif;
    font-weight: 700;
    font-size: 21px;
    color: var(--brand-blue);
  }
  .holder-title {
    position: absolute;
    left: 22px; top: 66px;
    font-size: 11.5px;
    color: var(--ink);
  }
  .company-name {
    position: absolute;
    left: 22px; top: 117px;
    font-family: "Amaranth", sans-serif;
    font-weight: 700;
    font-size: 14px;
    color: var(--brand-blue);
  }
  .contact-list {
    position: absolute;
    left: 22px; top: 142px;
    list-style: none;
  }
  .contact-list li {
    display: flex;
    align-items: center;
    gap: 8px;
    height: 17.6px;
    font-size: 12.5px;
    color: var(--ink);
  }
  .contact-list svg { width: 11px; height: 11px; fill: var(--brand-blue); flex: none; }
  .address {
    position: absolute;
    left: 22px; top: 233px;
    font-size: 12.5px;
    line-height: 17.6px;
    color: var(--ink);
    font-style: normal;
  }
  .card-front .wordmark {
    position: absolute;
    right: 24px; top: 236px;
    font-family: "Amaranth", sans-serif;
    font-weight: 700;
    font-size: 19px;
    color: var(--brand-blue);
  }
</style>
</head>
<body>

<section class="card card-back" aria-label="Card back">
  <div class="wordmark">Vantrell Forge Works</div>
  <div class="web-line">
    <span class="rule"></span>
    <span>www.vantrellforge.com</span>
    <span class="rule"></span>
  </div>
</section>

<section class="card card-front" aria-label="Card front">
  <h1 class="holder-name">Marcus Ellery Dunn</h1>
  <p class="holder-title">Managing Director</p>
  <h2 class="company-name">Vantrell Forge Works, Inc.</h2>
  <ul class="contact-list">
    <li>
      <svg viewBox="0 0 12 12" aria-hidden="true"><path d="M1 4c0-2 2-3 5-3s5 1 5 3v1H8.5V3.8h-5V5H1zM3 6h6l2 5H1z"/></svg>
      555-0142-2100 (VFW)
    </li>
    <li>
      <svg viewBox="0 0 12 12" aria-hidden="true"><path d="M3.5 0.5h5a1 1 0 0 1 1 1v9a1 1 0 0 1-1 1h-5a1 1 0 0 1-1-1v-9a1 1 0 0 1 1-1zM4 2v7h4V2zM5.5 9.6h1v1h-1z"/></svg>
      555-0187-3345
    </li>
    <li>
      <svg viewBox="0 0 12 12" aria-hidden="true"><path d="M3 0.5h6v3H3zM1 4h10v5H9v2.5H3V9H1zM4 7.5v3h4v-3z"/></svg>
      555-0163-4470
    </li>
    <li>
      <svg viewBox="0 0 12 12" aria-hidden="true"><path d="M0.5 2h11v8h-11zM1.5 3l4.5 3.5L10.5 3v-0.2h-9z"/></svg>
      www.vantrellforge.com
    </li>
    <li>
      <svg viewBox="0 0 12 12" aria-hidden="true"><circle cx="6" cy="6" r="5.2" fill="none" stroke="#0355a3" stroke-width="1.2"/><path d="M0.8 6h10.4M6 0.8c-2.6 3-2.6 7.4 0 10.4M6 0.8c2.6 3 2.6 7.4 0 10.4" fill="none" stroke="#0355a3" stroke-width="1"/></svg>
      mdunn@vantrellforge.com
    </li>
  </ul>
  <address class="address">812 Foundry Row, Millbrook,<br>Lakeview, US 482160</address>
  <div class="wordmark">Vantrell Forge Works</div>
</section>

</body>
</html>
```